Stylish Business Cards Wanted

- DOUBLE SIDED Design Required -

High end, edgy cards for a corporate and personal stylist. Must include logo,
Name: Belinda Harwick
Title: Director and Stylist
telephone : +61 8 7142 5809
email: belinda@theloombriefing.example
website: theloombriefing.example
Tag: Corporate Workwear & Uniform Specialist | Personal Stylist
Would like nice icons for telephone, email, website

Target Market(s)

Businesses wanting stylish uniforms, people wanting stylish wardrobes

Industry/Entity Type

Corporate Workwear Stylist

Contact Information for Business Card

I would like black, white and gold foiling incorporated in the design - possibly a touch of the other colours on my branding guide attached Name: Belinda Harwick Title: Director and Stylist telephone : +61 8 7142 5809 email: belinda@theloombriefing.example website: theloombriefing.example Tag: Corporate Workwear & Uniform Specialist | Personal Stylist Would like nice icons for telephone, email, website

Font styles to use
Other font styles liked:
• Raleway

Colors

Designer to choose colors to be used in the design.

Requirements
Must have
• Gold foil accents

```html
<!DOCTYPE html>
<html lang="en">
<head>
<meta charset="utf-8">
<title>The Loom Briefing — Business Card</title>
<link href="https://fonts.googleapis.com/css2?family=Roboto:wght@400&family=Satisfy&family=Dancing+Script:wght@500&display=swap" rel="stylesheet">
<style>
  :root {
    --backdrop: #e6e2dc;
    --card: #f4f2ef;
    --card-edge: #d9d5cf;
    --navy: #1d2236;
    --ink: #1a1a1a;
    --gold: #c9a24a;
    --rose: #c95b82;
  }
  * { margin: 0; padding: 0; box-sizing: border-box; }
  html, body {
    width: 1200px;
    height: 1054px;
    overflow: hidden;
    background: var(--backdrop);
  }
  .card {
    position: absolute;
    left: 100px;
    top: 224px;
    width: 1000px;
    height: 605px;
    background: linear-gradient(160deg, #f8f7f5 0%, var(--card) 60%, #eeebe7 100%);
    border: 1px solid var(--card-edge);
    border-radius: 22px;
    box-shadow: 0 10px 30px rgba(0,0,0,0.08);
  }
  .brand {
    position: absolute;
    left: 83px;
    top: 205px;
    width: 337px;
    text-align: center;
    font-family: "Roboto", sans-serif;
    font-weight: 400;
    font-size: 50px;
    line-height: 1.1;
    color: var(--navy);
  }
  .divider {
    position: absolute;
    left: 455px;
    top: 147px;
    width: 2px;
    height: 254px;
    background: var(--rose);
    opacity: 0.8;
  }
  .person-name {
    position: absolute;
    left: 506px;
    top: 138px;
    font-family: "Satisfy", cursive;
    font-size: 44px;
    color: var(--gold);
    white-space: nowrap;
  }
  .person-title {
    position: absolute;
    left: 506px;
    top: 208px;
    font-family: "Roboto", sans-serif;
    font-size: 24px;
    color: var(--ink);
  }
  .contact-list {
    position: absolute;
    left: 506px;
    top: 290px;
    list-style: none;
    font-family: "Roboto", sans-serif;
    font-size: 24px;
    color: var(--ink);
  }
  .contact-item {
    display: flex;
    align-items: center;
    height: 41px;
  }
  .contact-icon {
    width: 24px;
    height: 24px;
    margin-right: 20px;
    flex: none;
  }
  .tagline {
    position: absolute;
    left: 0;
    right: 0;
    top: 528px;
    text-align: center;
    font-family: "Dancing Script", cursive;
    font-weight: 500;
    font-size: 30px;
    color: var(--ink);
    white-space: nowrap;
  }
  .tagline .sep {
    color: var(--rose);
    margin: 0 14px;
  }
</style>
</head>
<body>
  <section class="card">
    <div class="brand">The Loom<br>Briefing</div>
    <div class="divider"></div>

    <h1 class="person-name">Belinda Harwick</h1>
    <p class="person-title">Director and Stylist</p>

    <ul class="contact-list">
      <li class="contact-item">
        <svg class="contact-icon" viewBox="0 0 24 24" fill="none" stroke="var(--gold)" stroke-width="1.6">
          <circle cx="12" cy="12" r="10"/>
          <path d="M9 7.5c-.8.3-1.5 1-1.3 2 .5 2.8 3 5.4 5.8 6 1 .2 1.7-.5 2-1.3l-1.8-1.2-1 .8c-1.2-.6-2.3-1.7-2.9-2.9l.8-1z" stroke-linejoin="round"/>
        </svg>
        <span>+61 8 7142 5809</span>
      </li>
      <li class="contact-item">
        <svg class="contact-icon" viewBox="0 0 24 24" fill="none" stroke="var(--gold)" stroke-width="1.6">
          <rect x="2.5" y="5.5" width="19" height="13" rx="1"/>
          <path d="M3 6.5l9 7 9-7M3 18l7-6M21 18l-7-6"/>
        </svg>
        <span>belinda@theloombriefing.example</span>
      </li>
      <li class="contact-item">
        <svg class="contact-icon" viewBox="0 0 24 24" fill="none" stroke="var(--gold)" stroke-width="1.6">
          <circle cx="12" cy="12" r="10"/>
          <ellipse cx="12" cy="12" rx="4.5" ry="10"/>
          <path d="M2 12h20M4 7h16M4 17h16"/>
        </svg>
        <span>www.theloombriefing.example</span>
      </li>
    </ul>

    <p class="tagline">Corporate Workwear &amp; Uniform Specialist<span class="sep">|</span>Personal Stylist</p>
  </section>
</body>
</html>
```